need corporate, modern business card created for Consulting Company

I need a slick business card using elements from my website, as well as, integrating my pixelforge-created logo (see files).

The business card needs to be:
1. Corporate and modern
2. Clean and professional

I've included a PSD with the logo/icon that you can use to create it. Feel free to try a metallic finish on the logo, make it bigger/small, underlay it. Whatever you need to do to make my card stand out.

Try a black background, or white background or gray.

The idea is for my card to be memorable as well as professional and corporate.

Target Market(s)

Corporate business in the US and Canada.

Industry/Entity Type

Business

Contact Information for Business Card

Commerce Advancing Methods
Martin Coles, Senior Partner
office: 1 877 555 0143
mobile: 1 519 555 0172
website: http://www.brightvale.example

Requirements
Must have
• Card-related information
• corporate, yet modern
• clean and professional
• incorporate the icon only
• must have an editable form when complete!
Nice to have
• metallic icon might be cool
• try it with white or black

```html
<!DOCTYPE html>
<html lang="en">
<head>
<meta charset="utf-8">
<title>Brightvale Business Card</title>
<link rel="stylesheet" href="https://fonts.googleapis.com/css2?family=Exo+2:wght@500;600;700&display=swap">
<style>
  :root {
    --brand-blue: #285eb4;
    --ink: #1b1b1f;
    --paper: #ffffff;
    --backdrop: #eeeff1;
    --soft-blue: #e3ebf7;
  }
  * { box-sizing: border-box; margin: 0; padding: 0; }
  html, body {
    width: 1200px; height: 800px; overflow: hidden;
    background: var(--backdrop);
    font-family: "Exo 2", sans-serif;
  }
  .canvas {
    position: relative; width: 1200px; height: 800px;
  }
  .card {
    position: absolute; width: 560px; height: 320px;
    border-radius: 4px;
    box-shadow: 0 6px 18px rgba(0,0,0,0.12);
    overflow: hidden;
  }
  .card-front { left: 90px; top: 60px; background: var(--paper); }
  .card-back  { left: 550px; top: 420px; background: var(--brand-blue); }

  .brand-symbol-area {
    position: absolute; left: 0; top: 150px; width: 250px; height: 170px;
    background: linear-gradient(135deg, var(--soft-blue), #c9d8ef);
    border-top-right-radius: 22px;
  }

  .wordmark {
    position: absolute; display: flex; align-items: center; gap: 8px;
    font-weight: 700; letter-spacing: 0.5px;
  }
  .wordmark .mark-square {
    width: 14px; height: 14px; border-radius: 3px;
  }
  .card-front .wordmark {
    left: 250px; top: 34px; font-size: 40px; color: var(--brand-blue);
  }
  .card-front .mark-square { background: var(--brand-blue); }

  .contact-block {
    position: absolute; left: 270px; top: 110px;
  }
  .person-name {
    font-size: 24px; font-weight: 700; color: var(--ink); line-height: 1.1;
  }
  .person-title {
    font-size: 15px; font-weight: 600; color: var(--brand-blue); margin-top: 2px;
  }
  .contact-list {
    list-style: none; margin-top: 22px;
  }
  .contact-list li {
    display: flex; align-items: center; gap: 9px;
    font-size: 15px; font-weight: 600; color: var(--ink);
    line-height: 1; margin-bottom: 8px;
  }
  .contact-icon {
    width: 17px; height: 17px; flex: none;
  }

  .card-back .wordmark {
    left: 0; right: 0; top: 0; bottom: 0; justify-content: center;
    font-size: 56px; color: var(--paper); font-weight: 600;
  }
  .card-back .mark-square { width: 22px; height: 22px; background: var(--paper); }
</style>
</head>
<body>
<main class="canvas">

  <section class="card card-front" aria-label="Business card front">
    <div class="brand-symbol-area" role="img" aria-label="Large brand symbol decoration"></div>

    <div class="wordmark"><span class="mark-square"></span>brightvale</div>

    <div class="contact-block">
      <p class="person-name">Martin Coles</p>
      <p class="person-title">Senior Partner</p>
      <ul class="contact-list">
        <li>
          <svg class="contact-icon" viewBox="0 0 16 16" aria-hidden="true">
            <rect width="16" height="16" rx="3" fill="#285eb4"/>
            <path d="M5 3.5l2 2-1 1.3a6 6 0 003.2 3.2l1.3-1 2 2-1.2 1.5C7.5 12.5 3.5 8.5 3.5 4.7z" fill="#fff"/>
          </svg>
          1 877 555 0143
        </li>
        <li>
          <svg class="contact-icon" viewBox="0 0 16 16" aria-hidden="true">
            <rect width="16" height="16" rx="3" fill="#285eb4"/>
            <rect x="5" y="2.5" width="6" height="11" rx="1.2" fill="#fff"/>
            <rect x="6.2" y="4" width="3.6" height="6.5" fill="#285eb4"/>
          </svg>
          1 519 555 0172
        </li>
        <li>
          <svg class="contact-icon" viewBox="0 0 16 16" aria-hidden="true">
            <rect width="16" height="16" rx="3" fill="#285eb4"/>
            <rect x="3" y="4.5" width="10" height="7" fill="#fff"/>
            <path d="M3 4.5l5 4 5-4" fill="none" stroke="#285eb4" stroke-width="1"/>
          </svg>
          info@brightvale.example
        </li>
        <li>
          <svg class="contact-icon" viewBox="0 0 16 16" aria-hidden="true">
            <rect width="16" height="16" rx="3" fill="#285eb4"/>
            <circle cx="8" cy="8" r="4.6" fill="none" stroke="#fff" stroke-width="1.2"/>
            <ellipse cx="8" cy="8" rx="2" ry="4.6" fill="none" stroke="#fff" stroke-width="1"/>
            <path d="M3.4 8h9.2" stroke="#fff" stroke-width="1"/>
          </svg>
          www.brightvale.example
        </li>
      </ul>
    </div>
  </section>

  <section class="card card-back" aria-label="Business card back">
    <div class="wordmark"><span class="mark-square"></span>brightvale</div>
  </section>

</main>
</body>
</html>
```